Smack you in the face - Landing page for Residential Electrical Repairs (Searchly Ads)

I need an effective landing page for Searchly ads. The ads will target residential electrical repairs. Lighting Outages, Power Outages, Breakers Tripping, Outlets Not Working. I need a strong call to action to Call Us Now! Forms don't work well for us so we only need one form as a last option at the bottom of the page. We only work on homes. the website is https://www.vantor-wiring.example/
email is : support@vantor-wiring.example
Phone 555-217-4086

**This is about one focused service. Electrical Repairs - That includes Partial Power Outages, Outlets Not Working, Tripped Breakers, Electrical Panel repairs, and Fusebox Repairs. The area served will only be Greenville, SC. KOBA is the platform

Target Market(s)

Homeonwers in need of electrical repair

Industry/Entity Type

Residential Electricians

Coding

Coded - Design and coding required

Requirements
Must have
• Strong to action for phone calls, this landing page must grab action fast.
Nice to have
• Social proof with existing 5 start reviews for Searchly, Rately, TCB, and Friendnet
Should not have
• Should not be form based. I do not like the site's current them, please don't copy it. Make your own.

```html
<!DOCTYPE html>
<html lang="en">
<head>
<meta charset="utf-8">
<title>Vantor Wiring – Residential Electrical Repairs</title>
<link href="https://fonts.googleapis.com/css2?family=Russo+One&family=Arimo:wght@400;700&display=swap" rel="stylesheet">
<style>
  :root{
    --navy:#161b36;
    --blue:#1a8fd8;
    --bar-blue:#2497c9;
    --orange:#ee8a2a;
    --grey-band:#b9babd;
    --ink:#1c1c1c;
    --page:#ffffff;
    --photo-tone:#c9cfd8;
  }
  html,body{margin:0;padding:0;width:1200px;height:1200px;overflow:hidden;background:var(--page);font-family:"Arimo",Arial,sans-serif;}
  .canvas{position:relative;width:1198px;height:1198px;border:1px solid #9a9a9a;}
  .banner{position:absolute;left:38px;top:304px;width:1124px;height:588px;overflow:hidden;
    background:radial-gradient(ellipse at 70% 55%, #ffffff 0%, #f3f4f6 100%);
    border:1px solid #cfcfcf;box-sizing:border-box;}
  .banner-art{position:absolute;left:0;top:0;width:1124px;height:588px;}
  .brand-box{position:absolute;left:496px;top:0;width:256px;height:106px;background:var(--navy);
    border-bottom-right-radius:4px;display:flex;align-items:center;justify-content:center;gap:10px;}
  .brand-mark{width:14px;height:14px;border-radius:50%;background:var(--bar-blue);}
  .brand-name{font-family:"Russo One",sans-serif;color:#fff;font-size:27px;letter-spacing:1px;}
  .location-bar{position:absolute;left:752px;top:0;width:372px;height:60px;background:var(--bar-blue);
    display:flex;align-items:center;padding-left:14px;gap:30px;box-sizing:border-box;}
  .location{display:flex;align-items:center;gap:6px;color:#fff;font-weight:700;font-size:9.4px;line-height:12px;}
  .location svg{width:12px;height:16px;flex:none;}
  .headline{position:absolute;left:576px;top:154px;margin:0;font-family:"Russo One",sans-serif;font-weight:400;
    color:var(--blue);font-size:31px;line-height:42px;letter-spacing:.6px;}
  .services{position:absolute;left:580px;top:238px;margin:0;padding:0;list-style:none;}
  .services li{font-size:21px;line-height:27px;color:var(--ink);padding-left:15px;position:relative;}
  .services li::before{content:"";position:absolute;left:0;top:6px;width:6px;height:6px;border-radius:50%;background:var(--blue);}
  .question{position:absolute;left:576px;top:398px;margin:0;font-size:20.5px;color:var(--ink);}
  .cta{position:absolute;left:576px;top:426px;width:256px;height:44px;background:var(--bar-blue);border-radius:3px;
    font-family:"Russo One",sans-serif;color:#fff;font-size:30px;line-height:44px;text-align:center;text-decoration:none;}
  .phone{position:absolute;left:576px;top:474px;width:256px;text-align:center;font-size:21px;color:var(--ink);text-decoration:none;}
  .legal{position:absolute;left:476px;top:546px;width:200px;text-align:center;color:var(--bar-blue);font-size:10px;line-height:12px;}
  .legal a{color:var(--bar-blue);text-decoration:none;}
</style>
</head>
<body>
<div class="canvas">
  <section class="banner">
    <svg class="banner-art" viewBox="0 0 1124 588" aria-hidden="false">
      <!-- footer band -->
      <rect x="0" y="528" width="1124" height="60" fill="var(--navy)"/>
      <!-- left frame bands -->
      <path d="M0 0 H486 C520 110 550 200 570 250 C580 280 570 300 540 330 L280 588 H0 Z" fill="var(--orange)"/>
      <path d="M0 0 H478 C508 110 534 200 552 250 C560 275 552 295 528 318 L250 588 H0 Z" fill="var(--grey-band)"/>
      <path d="M0 430 C80 480 160 520 250 540 L230 588 H0 Z" fill="var(--navy)"/>
      <path d="M0 470 C80 520 170 560 260 570 L250 588 H0 Z" fill="var(--orange)"/>
      <g role="img" aria-label="Photo of a smiling electrician in a blue uniform and cap working at an open breaker panel">
        <path d="M0 0 H462 C490 110 516 200 530 245 C537 270 528 288 508 308 L300 530 C220 520 110 480 0 440 Z" fill="var(--photo-tone)"/>
      </g>
      <!-- hexagons -->
      <polygon points="1010,454 994,480 964,480 948,454 964,428 994,428" fill="#1e8fde"/>
      <polygon points="903,566 890,588 864,588 851,566 864,544 890,544" fill="#ffffff"/>
      <g role="img" aria-label="Photo of a multimeter testing a wall outlet">
        <polygon points="982,496 952,548 892,548 862,496 892,444 952,444" fill="var(--orange)"/>
        <polygon points="974,496 948,541 896,541 870,496 896,451 948,451" fill="#a9adb4"/>
      </g>
      <g role="img" aria-label="Photo of a hand holding a circuit breaker">
        <polygon points="1126,524 1088,590 1012,590 974,524 1012,458 1088,458" fill="var(--orange)"/>
        <polygon points="1117,524 1083,582 1017,582 983,524 1017,466 1083,466" fill="#8f949c"/>
      </g>
    </svg>

    <div class="brand-box"><span class="brand-mark"></span><span class="brand-name">VANTOR WIRING</span></div>

    <div class="location-bar">
      <div class="location">
        <svg viewBox="0 0 12 16"><path d="M6 0C2.7 0 0 2.6 0 5.9 0 10 6 16 6 16s6-6 6-10.1C12 2.6 9.3 0 6 0zm0 8.3A2.4 2.4 0 1 1 6 3.5a2.4 2.4 0 0 1 0 4.8z" fill="#fff"/></svg>
        <span>418 Larkspur Ave STE 12<br>Greenville, SC 29615</span>
      </div>
      <div class="location">
        <svg viewBox="0 0 12 16"><path d="M6 0C2.7 0 0 2.6 0 5.9 0 10 6 16 6 16s6-6 6-10.1C12 2.6 9.3 0 6 0zm0 8.3A2.4 2.4 0 1 1 6 3.5a2.4 2.4 0 0 1 0 4.8z" fill="#fff"/></svg>
        <span>72 Marlow Bend Rd, STE 9<br>Raleigh, NC 27612</span>
      </div>
    </div>

    <h1 class="headline">YOUR TRUSTED SOURCE FOR<br>ELECTRICAL SOLUTIONS</h1>
    <ul class="services">
      <li>Residential Electrical Repairs</li>
      <li>Lighting Outages</li>
      <li>Power Outages</li>
      <li>Breakers Tripping</li>
      <li>Outlets Not Working</li>
    </ul>
    <p class="question">Do You Offer Electrical Panel Upgrades?</p>
    <a class="cta" href="tel:5552174086">CALL US NOW!</a>
    <a class="phone" href="tel:5552174086">555-217-4086</a>
    <div class="legal">Copyright © 2023 Client’s Various. All rights reserved<br><a href="#">Terms of Service</a> | <a href="#">Privacy Policy</a></div>
  </section>
</div>
</body>
</html>
```